Visitenkarten und Briefpapier
Zielgruppe
Planung und Realisierung von individuellen und wertbeständigen Kamin- und Ofenlösungen, sowie Fliesen- und Baddesign.
Aufgabenstellung
Wir benötigen ein möglichst schlichtes Design für Visitenkarten, bzw. Briefpapier. Für die Visitenkarten gerne auch Vorschläge mit Prägung, Ausstanzung oder mit Heißfolie. Auch Klappkarten wären denkbar. Das Design soll "das gewisse Etwas haben" und nicht zu verspielt sein.
Die Visitenkarten sind für die Firma KORVA, das Logo von der Ausstellung "raumfunke" soll dezent mit eingebunden werden (bei dem Briefpapier z.B. in der Fußzeile". Die farbliche Gestaltung sollte sich an den Farben des Logos orientieren.
Schriftart für Texte: Century Gothic
Schriftfarbe: RAL 7016
Nur eine Idee: Ich könnte mir auch gut vorstellen, dass die Visitenkarte aus einer Zündholzverpackung (wenn dann aber eine besondere mit nur einem Zündholz oder einem besonders breiten) besteht: http://glimmvelo.de/produkte_briefchen.php

```html
<!DOCTYPE html>
<html lang="de">
<head>
<meta charset="utf-8">
<title>KORVA – Visitenkarte</title>
<link rel="stylesheet" href="https://fonts.googleapis.com/css2?family=Questrial&display=swap">
<style>
  :root {
    --anthracite: #1d2a2f;
    --anthracite-soft: #3a4549;
    --slate: #4a5559;
    --flame: #c87000;
    --paper: #d9d9d9;
    --paper-edge: #cfcfcf;
    --text-light: #b8bdbf;
    --text-grey: #7d8487;
    --ground: #8e8f90;
  }
  * { box-sizing: border-box; margin: 0; padding: 0; }
  html, body { width: 1200px; height: 840px; overflow: hidden; }
  body {
    background: var(--ground);
    font-family: "Questrial", "Century Gothic", sans-serif;
    display: flex;
    align-items: center;
    justify-content: center;
    gap: 40px;
  }
  .card {
    width: 540px;
    height: 350px;
    border-radius: 18px;
    position: relative;
    overflow: hidden;
    box-shadow: 0 14px 30px rgba(0,0,0,.35);
  }
  /* Front */
  .card--front { background: var(--paper); }
  .front__dark {
    position: absolute; top: 0; right: 0; bottom: 0; width: 230px;
    background: linear-gradient(135deg, var(--anthracite-soft), var(--anthracite) 70%);
  }
  .front__band {
    position: absolute; top: 0; bottom: 0; left: 286px; width: 24px;
    background: var(--flame);
  }
  .wordmark {
    display: flex; flex-direction: column; gap: 2px;
    position: absolute; top: 46px; left: 40px;
  }
  .wordmark__name {
    font-size: 54px; letter-spacing: 4px; line-height: 1;
    color: var(--anthracite);
  }
  .wordmark__claim {
    font-size: 16px; letter-spacing: 1px; color: var(--anthracite);
  }
  .address {
    position: absolute; left: 40px; bottom: 36px;
    display: flex; align-items: center; gap: 12px;
    font-size: 17px; line-height: 1.2; color: var(--text-grey);
  }
  .person {
    position: absolute; top: 34px; right: 28px; text-align: right;
  }
  .person__name { font-size: 20px; color: var(--flame); }
  .person__role { font-size: 12px; color: var(--text-light); letter-spacing: .5px; }
  .contact {
    position: absolute; right: 24px; bottom: 40px;
    list-style: none; text-align: right;
    font-size: 15px; line-height: 1.75; color: var(--text-light);
  }
  .contact li { display: flex; align-items: center; justify-content: flex-end; gap: 10px; }
  .contact svg { width: 18px; height: 18px; }
  /* Back */
  .card--back {
    background: var(--anthracite);
    display: flex; align-items: center; justify-content: center;
  }
  .card--back .wordmark { position: static; align-items: center; }
  .card--back .wordmark__name { font-size: 80px; color: var(--paper); letter-spacing: 6px; }
  .card--back .wordmark__claim { font-size: 22px; color: var(--paper); }
</style>
</head>
<body>
  <article class="card card--front">
    <div class="front__band"></div>
    <div class="front__dark"></div>

    <div class="wordmark">
      <span class="wordmark__name">KORVA</span>
      <span class="wordmark__claim">kamine · öfen · fliesen</span>
    </div>

    <div class="address">
      <svg width="20" height="26" viewBox="0 0 20 26" aria-hidden="true">
        <path d="M10 0C4.5 0 0 4.4 0 9.8 0 17 10 26 10 26s10-9 10-16.2C20 4.4 15.5 0 10 0z" fill="var(--anthracite)"/>
        <circle cx="10" cy="9.5" r="3.6" fill="var(--paper)"/>
      </svg>
      <span>Am Lindenbach 12c<br>27630 Haldorf</span>
    </div>

    <div class="person">
      <div class="person__name">Jonas Brenner</div>
      <div class="person__role">Geschäftsführer</div>
    </div>

    <ul class="contact">
      <li>04120 / 73 18 40
        <svg viewBox="0 0 24 24" aria-hidden="true"><path d="M6.6 10.8a15 15 0 0 0 6.6 6.6l2.2-2.2a1 1 0 0 1 1-.25 11.4 11.4 0 0 0 3.6.57 1 1 0 0 1 1 1V20a1 1 0 0 1-1 1A17 17 0 0 1 3 4a1 1 0 0 1 1-1h3.5a1 1 0 0 1 1 1c0 1.25.2 2.45.57 3.57a1 1 0 0 1-.25 1z" fill="var(--text-light)"/></svg>
      </li>
      <li>04120 / 73 18 44
        <svg viewBox="0 0 24 24" aria-hidden="true"><path d="M6 3h12v5H6z M3 9h18v8h-3v4H6v-4H3z M8 14v5h8v-5z" fill="var(--text-light)"/></svg>
      </li>
      <li>info@korva-haldorf.de
        <svg viewBox="0 0 24 24" aria-hidden="true"><rect x="2.5" y="5.5" width="19" height="13" fill="none" stroke="var(--text-light)" stroke-width="1.5"/><path d="M2.5 5.5l9.5 7 9.5-7" fill="none" stroke="var(--text-light)" stroke-width="1.5"/></svg>
      </li>
    </ul>
  </article>

  <article class="card card--back">
    <div class="wordmark">
      <span class="wordmark__name">KORVA</span>
      <span class="wordmark__claim">kamine · öfen · fliesen</span>
    </div>
  </article>
</body>
</html>
```